Wed site for biomedical device startup

We need a generic website for a medical device startup. I will provide examples below of websites from other companies that can serve as models for what we are looking for. The startup is for a device that can non invasively measure blood flow in the brain using light. The application is to detect the type of stroke someone is having before they get to the hospital so treatment can be started right away. This saves patients upto hours of delayed treatment. Patients will be able to recover from stroke much better and faster as a result. I have attached an AI generated illustration of what the device will ultimately look like for reference.

https://www.372clinicaltech.com
https://vextalune.com

Target Market(s)

Biomedical, medical device, investors of biomedical device startups

Industry/Entity Type

Biomedical

Coding

Coded - Design and coding required

Number of Pages Required

4 page

Requirements
Must have
• same section and section headings as example websites listed above
Nice to have
• similar to example websites listed above. Prefer a darker website over a lighter one. Perhaps dark blues to go with logo colors. A moving background image element at top of landing page could be cool. Something indicative of heartbeat, or neurons, or blood flow.

```html
<!DOCTYPE html>
<html lang="en">
<head>
<meta charset="utf-8">
<title>Lumera — Biomedical Science</title>
<link href="https://fonts.googleapis.com/css2?family=Montserrat:wght@400;500;600;700&display=swap" rel="stylesheet">
<style>
:root{
  --navy:#0d0a4d;
  --navy-deep:#080636;
  --purple:#8a16d6;
  --violet:#5b2be0;
  --cyan:#26c6e6;
  --white:#ffffff;
  --muted:#d9d8f0;
  --grad:linear-gradient(90deg,#8a16d6 0%,#4f5fe6 55%,#26c6e6 100%);
}
*{box-sizing:border-box;margin:0;padding:0}
html,body{width:1200px;height:4713px;overflow:hidden}
body{background:var(--navy);font-family:'Montserrat',sans-serif;color:var(--white);position:relative}
.abs{position:absolute}
a{color:inherit;text-decoration:none}

/* nav */
.site-nav{left:0;top:0;width:1200px;height:84px;background:var(--navy-deep);z-index:5}
.brand{display:flex;align-items:center;gap:12px;font-weight:500;font-size:42px;letter-spacing:2px}
.brand-dot{width:58px;height:58px;border-radius:50%;background:var(--grad)}
.site-nav .brand{position:absolute;left:113px;top:13px}
.nav-link{position:absolute;top:34px;font-size:14px;font-weight:500;transform:translateX(-50%)}
.nav-link.active{font-weight:700;text-decoration:underline;text-underline-offset:5px}

/* hero */
.hero{left:0;top:84px;width:1200px;height:620px;overflow:hidden}
.hero-art{position:absolute;inset:0;background:radial-gradient(ellipse 420px 360px at 880px 220px,#2f5fb0 0%,#173a86 40%,transparent 75%),linear-gradient(180deg,#10205f 0%,#0e1a55 60%,var(--navy) 100%)}
.hero h1{position:absolute;left:113px;top:76px;font-size:39px;line-height:51px;font-weight:700;letter-spacing:.5px}
.btn-outline{position:absolute;left:113px;top:302px;width:171px;height:49px;border:2px solid var(--white);border-radius:25px;font-size:14px;font-weight:700;display:flex;align-items:center;justify-content:center}
.hero-wave{position:absolute;left:0;top:0;width:1200px;height:620px}

.heading{font-size:39px;font-weight:700;line-height:1.2}
.bar{height:5px;width:84px;border-radius:3px;background:linear-gradient(90deg,var(--purple),var(--cyan))}
.copy{font-size:14.5px;line-height:25.6px;color:var(--muted)}
.btn{height:48px;width:172px;border-radius:24px;background:var(--grad);font-size:14.5px;font-weight:700;display:flex;align-items:center;justify-content:center}
.photo{background:linear-gradient(135deg,#2b2a5a,#4b4f7c)}

/* about */
.about-photo{left:110px;top:750px;width:468px;height:534px;border-radius:24px;border:4px solid transparent;background:linear-gradient(135deg,#d8b4a0,#8c6e63 60%,#2a2c44) padding-box,linear-gradient(135deg,var(--purple),var(--cyan)) border-box}

/* partners */
.partners{left:0;top:1360px;width:1200px;height:480px}
.partner-box{position:absolute;top:1608px;width:187px;height:104px;border:2px solid rgba(255,255,255,.9);border-radius:8px}

/* contact */
.contact-bg{left:0;top:3430px;width:1200px;height:800px;background:radial-gradient(ellipse 500px 300px at 300px 200px,#1f1a6a 0%,transparent 70%),radial-gradient(ellipse 500px 350px at 950px 350px,#1c1860 0%,transparent 70%),var(--navy-deep)}
.field{position:absolute;border:2px solid var(--white);border-radius:24px;font-size:13px;font-weight:500;padding-left:18px;display:flex;align-items:center}
.field.area{align-items:flex-start;padding-top:16px;border-radius:14px}
.info-icon{position:absolute;left:640px;width:52px;height:52px;border:2px solid var(--white);border-radius:50%;display:flex;align-items:center;justify-content:center}
.info-title{position:absolute;left:715px;font-size:19px;font-weight:700}
.info-text{position:absolute;left:715px;font-size:16.5px;line-height:29px}

/* footer */
.foot-title{position:absolute;font-size:19px;font-weight:600}
.foot-list{position:absolute;list-style:none;font-size:15px;line-height:31.8px}
.social{position:absolute;top:4474px;width:36px;height:36px;border:2px solid var(--white);border-radius:50%}
</style>
</head>
<body>

<header class="site-nav abs">
  <div class="brand"><span class="brand-dot"></span>LUMERA</div>
  <a class="nav-link active" style="left:498px">HOME</a>
  <a class="nav-link" style="left:602px">ABOUT</a>
  <a class="nav-link" style="left:732px">TECHNOLOGY</a>
  <a class="nav-link" style="left:873px">FEATURES</a>
  <a class="nav-link" style="left:1008px">CONTACT US</a>
</header>

<section class="hero abs">
  <div class="hero-art" role="img" aria-label="Glowing blue digital profile of a human head made of light particles"></div>
  <svg class="hero-wave" viewBox="0 0 1200 620">
    <defs>
      <linearGradient id="heroLine" x1="0" x2="1"><stop offset="0" stop-color="#8a16d6"/><stop offset="0.55" stop-color="#5b2be0"/><stop offset="1" stop-color="#26c6e6"/></linearGradient>
    </defs>
    <path d="M0 470 C120 410 260 400 380 460 C500 520 560 590 680 570 C800 550 880 470 1000 490 C1100 505 1160 520 1200 530 L1200 620 L0 620 Z" fill="#0d0a4d"/>
    <path d="M0 470 C120 410 260 400 380 460 C500 520 560 590 680 570 C800 550 880 470 1000 490 C1100 505 1160 520 1200 530" fill="none" stroke="url(#heroLine)" stroke-width="7"/>
  </svg>
  <h1>TRANSFORMING<br>BIOMEDICAL SCIENCE<br>INTO LIFE-CHANGING<br>SOLUTIONS</h1>
  <a class="btn-outline">GET STARTED</a>
</section>

<section class="about">
  <div class="about-photo abs" role="img" aria-label="Clinician placing a light-based brain sensor on a patient's forehead beside a handheld monitor"></div>
  <h2 class="heading abs" style="left:640px;top:814px">ABOUT US</h2>
  <div class="bar abs" style="left:642px;top:882px"></div>
  <p class="copy abs" style="left:644px;top:912px;width:420px">Lorem Ipsum is simply dummy text of the printing and typesetting industry. Lorem Ipsum has been the industry's standard dummy text ever since the 1500s, when an unknown printer took a galley of type and scrambled it to make a type specimen book. It has survived not only five centuries, but also the leap into electronic typesetting, remaining essentially unchanged. It was popularised in the 1960s with the release of Letraset sheets containing Lorem Ipsum</p>
  <a class="btn abs" style="left:653px;top:1180px">LEARN MORE</a>
</section>

<section>
  <svg class="partners abs" viewBox="0 0 1200 480">
    <defs>
      <linearGradient id="bandFill" x1="0" x2="1"><stop offset="0" stop-color="#8a16d6"/><stop offset="0.5" stop-color="#4f6fe6"/><stop offset="1" stop-color="#22c7e2"/></linearGradient>
    </defs>
    <path d="M0 20 C200 -10 420 40 620 30 C820 20 980 60 1200 28 L1200 420 C1050 470 900 440 700 450 C480 460 260 420 0 455 Z" fill="url(#bandFill)"/>
  </svg>
  <h2 class="heading abs" style="left:0;width:1200px;top:1470px;text-align:center;font-size:38px">PARTNERS AND COLLABORATORS</h2>
  <div class="bar abs" style="left:556px;top:1535px;width:88px;background:linear-gradient(90deg,#8a16d6 45%,#26c6e6 55%)"></div>
  <div class="partner-box" style="left:106px"></div>
  <div class="partner-box" style="left:306px"></div>
  <div class="partner-box" style="left:503px"></div>
  <div class="partner-box" style="left:708px"></div>
  <div class="partner-box" style="left:904px"></div>
</section>

<section class="features">
  <h2 class="heading abs" style="left:112px;top:1992px">HOW WE HELP</h2>
  <div class="bar abs" style="left:112px;top:2060px"></div>
  <p class="copy abs" style="left:112px;top:2098px;width:420px">Lorem Ipsum is simply dummy text of the printing and typesetting industry. Lorem Ipsum has been the industry's standard dummy text ever since the 1500s, when an unknown printer took a galley of type and scrambled it to make a type specimen book.</p>
  <a class="btn abs" style="left:112px;top:2261px">LEARN MORE</a>
  <div class="photo abs" style="left:598px;top:1941px;width:494px;height:463px;background:linear-gradient(135deg,#1c2a52,#6d7fa6 55%,#d9dde6)" role="img" aria-label="Scientist in safety glasses working at a laboratory microscope"></div>

  <div class="photo abs" style="left:108px;top:2404px;width:492px;height:461px;background:radial-gradient(circle at 45% 40%,#3f8a6e,#13402f 60%,#0a2219)" role="img" aria-label="Close-up of green molecular chain structure"></div>
  <h2 class="heading abs" style="left:640px;top:2462px;font-size:37px;line-height:47px">LIFE-CHANGING<br>TECHNOLOGY FOR<br>PREMATURE INFANTS</h2>
  <div class="bar abs" style="left:642px;top:2627px"></div>
  <p class="copy abs" style="left:641px;top:2663px;width:430px">Lorem Ipsum is simply dummy text of the printing and typesetting industry.</p>
  <a class="btn abs" style="left:640px;top:2737px">LEARN MORE</a>

  <h2 class="heading abs" style="left:110px;top:2940px">NIRDS EXPLAINED</h2>
  <div class="bar abs" style="left:110px;top:3002px"></div>
  <p class="copy abs" style="left:110px;top:3035px;width:430px">Lorem Ipsum is simply dummy text of the printing and typesetting industry. Lorem Ipsum has been the industry's standard dummy text ever since the 1500s, when an unknown printer took a galley of type and scrambled it to make a type specimen book.</p>
  <a class="btn abs" style="left:110px;top:3205px">LEARN MORE</a>
  <div class="photo abs" style="left:598px;top:2865px;width:494px;height:463px;background:radial-gradient(circle at 70% 75%,#ff7a2a,#c0306a 30%,#4a2aa8 60%,#120a3a)" role="img" aria-label="Glowing neuron cells with branching blue and red fibres"></div>
</section>

<section class="contact">
  <div class="contact-bg abs" role="img" aria-label="Faint dark network of neurons in the background"></div>
  <h2 class="heading abs" style="left:0;width:1200px;top:3553px;text-align:center;font-size:38px">CONTACT US</h2>
  <div class="bar abs" style="left:556px;top:3620px;width:88px"></div>

  <div class="field" style="left:126px;top:3670px;width:459px;height:48px">NAME</div>
  <div class="field" style="left:126px;top:3736px;width:224px;height:47px">CONTACT NUMBER</div>
  <div class="field" style="left:364px;top:3736px;width:224px;height:47px">EMAIL ADDRESS</div>
  <div class="field area" style="left:128px;top:3798px;width:460px;height:115px">YOUR MESSAGE</div>
  <a class="btn abs" style="left:128px;top:3935px;width:216px;height:46px;font-size:15.5px">SEND MESSAGE</a>

  <div class="abs" style="left:640px;top:3674px;font-size:22px;font-weight:500">Contact Information</div>

  <div class="info-icon" style="top:3740px"><svg width="24" height="24" viewBox="0 0 24 24" fill="none" stroke="#fff" stroke-width="1.6"><path d="M5 3h4l2 5-2.5 1.5a11 11 0 0 0 6 6L16 13l5 2v4a2 2 0 0 1-2 2A16 16 0 0 1 3 5a2 2 0 0 1 2-2z"/></svg></div>
  <div class="info-title" style="top:3728px">CALL US</div>
  <div class="info-text" style="top:3755px">+1 555 014 2290</div>

  <div class="info-icon" style="top:3818px"><svg width="24" height="24" viewBox="0 0 24 24" fill="none" stroke="#fff" stroke-width="1.6"><rect x="3" y="6" width="18" height="13" rx="1"/><path d="M3 7l9 6 9-6"/></svg></div>
  <div class="info-title" style="top:3806px">EMAIL US</div>
  <div class="info-text" style="top:3833px">hello@lumeramed.com</div>

  <div class="info-icon" style="top:3897px"><svg width="24" height="24" viewBox="0 0 24 24" fill="none" stroke="#fff" stroke-width="1.6"><path d="M12 21s-7-6.5-7-12a7 7 0 0 1 14 0c0 5.5-7 12-7 12z"/><circle cx="12" cy="9" r="2.5"/></svg></div>
  <div class="info-title" style="top:3885px">OUR LOCATION</div>
  <div class="info-text" style="top:3912px">2025,Lorem Ipsum is simply<br>dummy text of the printing</div>

  <svg class="abs" style="left:0;top:4020px" width="1200" height="230" viewBox="0 0 1200 230">
    <defs>
      <linearGradient id="footLine" x1="0" x2="1"><stop offset="0" stop-color="#8a16d6"/><stop offset="0.5" stop-color="#4f6fe6"/><stop offset="1" stop-color="#26c6e6"/></linearGradient>
    </defs>
    <path d="M0 90 C200 120 320 30 560 20 C760 12 860 120 1000 190 C1080 225 1150 200 1200 170 L1200 230 L0 230 Z" fill="#0d0a4d"/>
    <path d="M0 90 C200 120 320 30 560 20 C760 12 860 120 1000 190 C1080 225 1150 200 1200 170" fill="none" stroke="url(#footLine)" stroke-width="7"/>
  </svg>
</section>

<footer>
  <div class="brand abs" style="left:113px;top:4272px;font-size:38px"><span class="brand-dot" style="width:56px;height:56px"></span>LUMERA</div>

  <div class="foot-title" style="left:412px;top:4272px">MAIN LINKS</div>
  <ul class="foot-list" style="left:407px;top:4322px"><li>Home</li><li>About</li><li>Technology</li><li>Features</li><li>Contact Us</li></ul>

  <div class="foot-title" style="left:624px;top:4272px">OTHER LINKS</div>
  <ul class="foot-list" style="left:620px;top:4322px"><li>Privacy policy</li><li>Contact information</li><li>Terms of service</li></ul>

  <div class="foot-title" style="left:880px;top:4270px;width:192px;text-align:center;line-height:26px">SUBSCRIBE TO<br>OUR EMAILS</div>
  <div class="abs" style="left:873px;top:4351px;width:216px;height:44px;background:#fff;border-radius:6px;color:#333;font-size:12px;padding-left:10px;display:flex;align-items:center">Your Email Address
    <span style="position:absolute;right:2px;top:2px;width:48px;height:40px;background:var(--navy);border-radius:4px;display:flex;align-items:center;justify-content:center">
      <svg width="22" height="22" viewBox="0 0 24 24" fill="none" stroke="#fff" stroke-width="1.6"><path d="M21 3L3 10l7 3 3 7 8-17z"/><path d="M10 13l11-10"/></svg>
    </span>
  </div>
  <div class="foot-title" style="left:880px;top:4428px;width:192px;text-align:center">FOLLOW US ON</div>
  <span class="social" style="left:941px"></span>
  <span class="social" style="left:990px"></span>

  <div class="abs" style="left:110px;top:4550px;width:978px;height:1px;background:rgba(255,255,255,.35)"></div>
  <div class="abs" style="left:0;width:1195px;top:4576px;text-align:center;font-size:13px">© 2025 Lumera I All Rights Reserved</div>
</footer>

</body>
</html>
```